Design Startseite Kanzlei-Homepage
Zielgruppe
Wir sind eine Rechtsanwaltskanzlei in Kempten (Allgäu) und regional sowie überregional in verschiedenen Rechtsgebieten tätig. Unsere Zielgruppe sind sowohl private als auch gewerbliche Mandanten.
Aufgabenstellung
Die bestehende Gestaltung wirkt derzeit aus unserer Sicht überholt. Insbesondere soll das bislang dominierende Rot vollständig entfallen.
Stattdessen stellen wir uns ein modernes, hochwertiges Erscheinungsbild vor, primär in dunklen Farbtönen (Anthrazit/Schwarz) kombiniert mit Beige- bzw. warmen Naturtönen. Ziel ist eine klare visuelle Anlehnung an unsere Kanzleiräumlichkeiten (siehe Fotos).
Die Webseite soll insgesamt moderner, klarer und visuell anspruchsvoller wirken, ohne an Seriosität und Zugänglichkeit einzubüßen. Die Balance zwischen hochwertigem Erscheinungsbild und mandantenorientierter Nutzerführung steht für uns im Vordergrund.

```html
<!DOCTYPE html>
<html lang="de">
<head>
<meta charset="utf-8">
<title>Kanzlei am Lindenhof – Startseite</title>
<link rel="stylesheet" href="https://fonts.googleapis.com/css2?family=Baskervville&family=Raleway:wght@400;500;600;700&display=swap">
<style>
:root{
  --black:#0c0c0c;
  --dark:#1b1a1a;
  --card:#262525;
  --band:#232222;
  --gold:#c7a27a;
  --text:#ffffff;
  --muted:#d8d3cc;
  --line:#7d6a55;
}
*{box-sizing:border-box;margin:0;padding:0}
html,body{width:1200px;height:2529px;overflow:hidden}
body{background:var(--dark);color:var(--text);font-family:"Raleway",sans-serif;position:relative}
.abs{position:absolute}
.serif{font-family:"Baskervville",serif;font-weight:400}
.eyebrow{font-size:11.5px;font-weight:600;color:var(--gold);letter-spacing:.3px;text-transform:uppercase}
.gold{color:var(--gold)}
.photo{position:absolute}
.btn-outline{position:absolute;border:2px solid var(--gold);color:#fff;font-size:12.5px;font-weight:600;letter-spacing:.6px;display:flex;align-items:center;justify-content:center;text-transform:uppercase}
/* header */
.site-header{position:absolute;left:0;top:0;width:1200px;height:79px;background:var(--black)}
.brand{position:absolute;font-weight:700;letter-spacing:.2px;color:#fff;white-space:nowrap}
.nav span{position:absolute;top:39px;font-size:12px;font-weight:600;white-space:nowrap}
.cta-top{position:absolute;left:930px;top:17px;width:188px;height:43px;background:var(--gold);color:#fff;font-size:12px;font-weight:700;letter-spacing:.8px;display:flex;align-items:center;justify-content:center}
/* cards */
.area-card{position:absolute;top:1002px;width:233px;height:236px;background:var(--card);text-align:center}
.area-card svg{position:absolute;left:50%;top:18px;transform:translateX(-50%)}
.area-card h3{position:absolute;top:88px;width:100%;font-size:14.5px;font-weight:500;letter-spacing:.4px}
.area-card p{position:absolute;top:118px;left:12px;right:12px;font-size:12.5px;line-height:19.5px;color:var(--muted)}
.area-card .more{position:absolute;top:195px;width:100%;font-size:12px;font-weight:600;color:var(--gold)}
/* lawyers */
.lawyer{position:absolute;top:1689px;width:163px}
.lawyer .portrait{width:163px;height:195px;border:1px solid var(--line)}
.lawyer .name{font-size:14px;margin-top:16px;padding-left:8px;white-space:nowrap}
.lawyer .role{font-size:11px;line-height:15px;color:var(--muted);margin-top:10px;padding-left:8px}
.lawyer .link{position:absolute;top:297px;left:8px;font-size:11px;font-weight:700;color:var(--gold)}
/* contact */
.contact-row{position:absolute;left:561px;font-size:14px;line-height:21px}
.contact-row svg{position:absolute;left:0}
.contact-row div{position:absolute;left:44px;white-space:nowrap}
/* footer */
.site-footer{position:absolute;left:0;top:2343px;width:1200px;height:157px;background:var(--black)}
.foot-col{position:absolute;top:20px;font-size:12px;line-height:16.5px}
.foot-col h4{font-size:11.5px;line-height:14px;font-weight:600;color:var(--gold);margin-bottom:4px}
.legal{position:absolute;left:0;top:2500px;width:1200px;height:29px;background:#151414;font-size:8.5px}
</style>
</head>
<body>

<header class="site-header">
  <div class="brand" style="left:55px;top:31px;font-size:19px">KANZLEI AM LINDENHOF</div>
  <nav class="nav">
    <span style="left:369px">Kanzlei ⌄</span>
    <span style="left:440px">Rechtsgebiete ⌄</span>
    <span style="left:545px">Anwälte ⌄</span>
    <span style="left:628px">Kontakt</span>
  </nav>
  <div class="cta-top">TERMIN VEREINBAREN</div>
</header>

<div class="photo" role="img" aria-label="Foto des Empfangsbereichs der Kanzlei mit Holzvertäfelung und beleuchtetem Tresen" style="left:0;top:79px;width:1200px;height:424px;background:linear-gradient(100deg,#3a2414 0%,#9b6a3e 22%,#c8c6c0 45%,#e4e2dd 60%,#9b7048 80%,#2c1a0f 100%)"></div>

<!-- Willkommen -->
<div class="eyebrow abs" style="left:106px;top:548px">Willkommen bei der Kanzlei am Lindenhof</div>
<h1 class="serif abs" style="left:106px;top:573px;font-size:32px;line-height:42px">Ihr Anliegen.<br>Unsere <span class="gold">Kompetenz.</span></h1>
<p class="abs" style="left:106px;top:668px;width:400px;font-size:12px;line-height:18.5px;font-weight:500">Wir beraten und vertreten Privatpersonen sowie Unternehmen in ausgewählten Rechtsgebieten - persönlich, strukturiert und mit klarem Fokus auf Ihre Ziele.</p>
<p class="abs" style="left:106px;top:740px;width:425px;font-size:12px;line-height:18.5px;font-weight:500">Unsere Kanzlei verbindet juristische Präzision mit einem modernen Verständnis von Dienstleistung. Wir nehmen uns Zeit für ihr Anliegen und entwickeln Lösungen, die rechtlich, wirtschaftlich und menschlich überzeugen.</p>
<svg class="abs" style="left:104px;top:829px" width="28" height="24" viewBox="0 0 28 24" fill="none" stroke="#c7a27a" stroke-width="2"><rect x="2" y="4" width="18" height="18" rx="2"/><path d="M7 12l5 5L26 2"/></svg>
<div class="abs gold" style="left:145px;top:834px;font-size:13px;font-weight:500">Persönlich. Verbindlich. Lösungsorientiert.</div>
<div class="photo" role="img" aria-label="Foto des Wartebereichs mit Sitzbank und großem Bergpanorama an der Wand" style="left:550px;top:504px;width:600px;height:365px;background:linear-gradient(90deg,#cfc8bc 0%,#a5744a 30%,#6b6c70 55%,#1a1a1c 75%,#8a6038 100%)"></div>

<!-- Rechtsgebiete -->
<div class="eyebrow abs" style="left:0;width:1200px;text-align:center;top:933px">Unsere Rechtsgebiete</div>
<h2 class="serif abs" style="left:0;width:1200px;text-align:center;top:950px;font-size:26px">Kompetent in vielen Bereichen.</h2>

<div class="area-card" style="left:103px">
  <svg width="54" height="54" viewBox="0 0 54 54" fill="none" stroke="#c7a27a" stroke-width="1.8"><path d="M27 8v38M14 46h26M10 16h34M10 16l-6 16h12zM44 16l-6 16h12zM4 32a6 4 0 0 0 12 0M38 32a6 4 0 0 0 12 0"/><circle cx="27" cy="10" r="3"/></svg>
  <h3>ARBEITSRECHT</h3>
  <p>Wir vertreten Arbeitgeber und Arbeitnehmer in allen Fragen und Arbeitsrechts.</p>
  <div class="more">MEHR ERFAHREN &nbsp; &gt;</div>
</div>
<div class="area-card" style="left:355px">
  <svg width="54" height="54" viewBox="0 0 54 54" fill="none" stroke="#c7a27a" stroke-width="1.8"><circle cx="19" cy="9" r="4"/><circle cx="35" cy="9" r="4"/><path d="M13 16h12v16h-2v18h-8V32h-2zM29 16h12v16h-2v18h-8V32h-2z"/><circle cx="27" cy="28" r="3"/></svg>
  <h3>FAMILIENRECHT</h3>
  <p>Einfühlsam und durchsetzungsstark - wir stehen Ihnen in familären Angelegenheiten zur Seite.</p>
  <div class="more">MEHR ERFAHREN &nbsp; &gt;</div>
</div>
<div class="area-card" style="left:607px">
  <svg width="58" height="54" viewBox="0 0 58 54" fill="none" stroke="#c7a27a" stroke-width="2"><path d="M4 28L29 5l25 23M10 23v27h38V23M24 50V34h10v16M41 12v-6h6v12"/></svg>
  <h3>MIETRECHT</h3>
  <p>Ob Mieter oder Vermieter - wir sorgen für rechtssichere Lösungen bei allen Mietfragen.</p>
  <div class="more">MEHR ERFAHREN &nbsp; &gt;</div>
</div>
<div class="area-card" style="left:858px">
  <svg width="54" height="54" viewBox="0 0 54 54" fill="none" stroke="#c7a27a" stroke-width="1.8"><rect x="4" y="14" width="46" height="32" rx="2"/><path d="M20 14V8h14v6M4 28h46"/><rect x="24" y="25" width="6" height="6"/></svg>
  <h3>WIRTSCHAFTRECHT</h3>
  <p>Wir begleiten Unternehmer in rechtlichen und wirtschaftlichen Herausforderungen.</p>
  <div class="more">MEHR ERFAHREN &nbsp; &gt;</div>
</div>
<div class="btn-outline" style="left:471px;top:1256px;width:250px;height:45px">Alle Rechtsgebiete ansehen</div>

<!-- Video -->
<div class="abs" style="left:0;top:1323px;width:1200px;height:272px;background:var(--band)"></div>
<div class="photo" role="img" aria-label="Video-Vorschaubild: Abendansicht des Kanzleigebäudes" style="left:56px;top:1324px;width:542px;height:271px;background:linear-gradient(160deg,#5a6b80 0%,#3a3a3e 45%,#6a5840 75%,#2a2624 100%)"></div>
<svg class="abs" style="left:275px;top:1419px" width="82" height="82" viewBox="0 0 82 82"><circle cx="41" cy="41" r="39" fill="#c7a27a" fill-opacity=".85" stroke="#fff" stroke-width="2"/><path d="M32 26l24 15-24 15z" fill="#fff"/></svg>
<div class="eyebrow abs" style="left:667px;top:1356px">Kanzlei am Lindenhof</div>
<h2 class="serif abs" style="left:667px;top:1380px;font-size:30px;line-height:37px">Vertrauen entsteht<br>im persönlichen Gespräch.</h2>
<p class="abs" style="left:667px;top:1474px;width:320px;font-size:12.5px;line-height:18px">Erfahren Sie mehr über unsere Kanzlei, unsere Werte und unsere Arbeitsweise.</p>
<div class="btn-outline" style="left:666px;top:1525px;width:149px;height:45px">Video ansehen</div>

<!-- Anwälte -->
<div class="eyebrow abs" style="left:333px;top:1617px">Ihre Anwälte</div>
<h2 class="serif abs" style="left:248px;top:1637px;font-size:29px">Persönlich für Sie da.</h2>

<div class="lawyer" style="left:57px">
  <div class="portrait" role="img" aria-label="Porträtfoto Walter Brunnhuber" style="background:linear-gradient(#f2f2f2,#d9d4cf)"></div>
  <div class="name">Walter Brunnhuber</div>
  <div class="role">freier Mitarbeiter</div>
  <div class="link">ZUM PROFIL &nbsp;&nbsp;&nbsp; &gt;</div>
</div>
<div class="lawyer" style="left:243px">
  <div class="portrait" role="img" aria-label="Porträtfoto Emre Kaplanoğlu" style="background:linear-gradient(#eeeeee,#3a3d44)"></div>
  <div class="name">Emre Kaplanoğlu</div>
  <div class="role">Rechtsanwalt<br>Fachanwalt für Familienrecht</div>
  <div class="link">ZUM PROFIL &nbsp;&nbsp;&nbsp; &gt;</div>
</div>
<div class="lawyer" style="left:428px">
  <div class="portrait" role="img" aria-label="Porträtfoto Sabine Wetterling" style="background:linear-gradient(#f0f0f0,#a9bcc1)"></div>
  <div class="name">Sabine Wetterling</div>
  <div class="role">Rechtsanwalt<br>Fachanwalt für Arbeitsrecht,<br>Erbrecht und Verkehrsrecht</div>
  <div class="link">ZUM PROFIL &nbsp;&nbsp;&nbsp; &gt;</div>
</div>
<div class="lawyer" style="left:611px">
  <div class="portrait" role="img" aria-label="Porträtfoto Tobias Rauchfuß" style="background:linear-gradient(#f2f2f2,#2a3560)"></div>
  <div class="name">Tobias Rauchfuß</div>
  <div class="role">freier Mitarbeiter</div>
  <div class="link">ZUM PROFIL &nbsp;&nbsp;&nbsp; &gt;</div>
</div>

<div class="eyebrow abs" style="left:912px;top:1637px">Mandantenüberzeugen</div>
<h2 class="serif abs" style="left:912px;top:1656px;font-size:29px;line-height:32px">Das sagen unsere<br>Mandanten.</h2>
<div class="abs" style="left:840px;top:1737px;width:310px;height:177px;border:1px solid var(--line)"></div>
<div class="abs" style="left:935px;top:1748px;font-size:24px;color:#e9b54a;letter-spacing:1px">★★★★★</div>
<p class="abs" style="left:870px;top:1790px;width:265px;font-size:13px;line-height:21px;font-weight:600">„Schnelle, klare und äußerst kompetente Beratung. Ich habe mich jederzeit gut aufgehoben gefühlt.“</p>
<div class="abs" style="left:928px;top:1870px;font-size:12px;font-weight:600">- Mandat über Rezensio</div>
<svg class="abs" style="left:1108px;top:1869px" width="24" height="24"><circle cx="12" cy="12" r="11" fill="none" stroke="#c7a27a" stroke-width="2"/></svg>
<div class="btn-outline" style="left:898px;top:1937px;width:193px;height:45px;border-width:1px;font-size:12px">Weitere Bewertungen</div>
<svg class="abs" style="left:972px;top:1995px" width="44" height="8"><circle cx="4" cy="4" r="2.5" fill="#fff"/><circle cx="22" cy="4" r="2.5" fill="#777"/><circle cx="39" cy="4" r="2.5" fill="#777"/></svg>

<!-- Kontakt -->
<div class="abs" style="left:0;top:2016px;width:1200px;height:1px;background:var(--line)"></div>
<div class="photo" role="img" aria-label="Dunkle Stadtkarte mit Lage der Kanzlei" style="left:20px;top:2034px;width:503px;height:288px;background:linear-gradient(135deg,#2e2e2e,#1f1f1f 60%,#2a2a2a)"></div>
<div class="eyebrow abs" style="left:561px;top:2072px">Kontakt &amp; Standort</div>
<h2 class="serif abs" style="left:561px;top:2092px;font-size:26px;letter-spacing:1px">Wir sind für Sie da.</h2>
<div class="contact-row" style="top:2126px">
  <svg width="24" height="28" viewBox="0 0 24 28" fill="none" stroke="#c7a27a" stroke-width="1.6" style="top:4px"><path d="M12 26s9-9 9-15a9 9 0 0 0-18 0c0 6 9 15 9 15z"/><circle cx="12" cy="11" r="3.5"/></svg>
  <div style="top:2px">Kanzlei am Lindenhof<br>Lindenhofgasse 7<br>87435 Kempten (Allgäu)</div>
</div>
<div class="contact-row" style="top:2196px">
  <svg width="28" height="26" viewBox="0 0 28 26" fill="none" stroke="#c7a27a" stroke-width="1.6"><path d="M6 2l5 5-3 4c2 4 5 7 9 9l4-3 5 5-3 3C12 24 2 14 3 5z"/></svg>
  <div style="top:2px">+49 831 555 204 70</div>
</div>
<div class="contact-row" style="top:2232px">
  <svg width="28" height="20" viewBox="0 0 28 20" fill="none" stroke="#c7a27a" stroke-width="1.6"><rect x="1" y="1" width="26" height="18"/><path d="M1 1l13 11L27 1M1 19l10-9M27 19l-10-9"/></svg>
  <div style="top:-1px">info@kanzlei-lindenhof.de</div>
</div>
<div class="contact-row" style="top:2262px">
  <svg width="26" height="26" viewBox="0 0 26 26" fill="none" stroke="#c7a27a" stroke-width="1.6"><circle cx="13" cy="13" r="11"/><path d="M13 6v7h6"/></svg>
  <div style="top:4px">Mo. - Fr.: &nbsp;&nbsp;&nbsp; 09:00 - 12:00, Uhr<br><span style="padding-left:73px">14:00 - 17:00 Uhr</span></div>
</div>
<div class="abs" style="left:872px;top:2064px;width:225px;height:247px;background:var(--gold)"></div>
<div class="abs" style="left:899px;top:2104px;font-size:13px;line-height:20px;font-weight:500;color:#fff">VEREINBAREN SIE<br>EINEN TERMIN.</div>
<div class="abs" style="left:897px;top:2166px;font-size:13px;line-height:20px;color:#fff">Wir nehmen und Zeit<br>für Ihr Anliegen.</div>
<div class="abs" style="left:895px;top:2229px;width:181px;height:60px;background:#111;color:#fff;font-size:13.5px;font-weight:500;letter-spacing:.5px;text-align:center;display:flex;align-items:center;justify-content:center;line-height:20px">JETZT KONTAKT<br>AUFNEHMEN</div>

<!-- Footer -->
<footer class="site-footer">
  <div class="brand" style="left:55px;top:20px;font-size:18px">KANZLEI AM LINDENHOF</div>
  <div class="abs" style="left:55px;top:75px;font-size:12px;line-height:17px">Ihre Rechtsanwaltskanzlei in Kempten.<br>Kompetent. Persnönlichh. Lösungsorientiert</div>
  <div class="foot-col" style="left:409px"><h4>NAVIAGTION</h4>Rechtsanwälte<br>Mitarbeiter<br>Karriere<br>Downloads<br>Bewertungen</div>
  <div class="foot-col" style="left:614px"><h4>RECHTGEBIETE</h4>Familienrecht<br>Arbeitsrecht<br>Verkehrsrecht<br>Strafrecht<br>Erbrecht<br>Mietrecht<br>Baurecht</div>
  <div class="foot-col" style="left:826px;font-size:11.5px"><h4>KONTAKT</h4>Kanzlei am Lindenhof<br>Lindenhofgasse 7<br>87435 Kempten (Allgäu)<br><br>+49 831 555 204 70<br><br>info@kanzlei-lindenhof.de</div>
</footer>
<div class="legal">
  <span class="abs" style="left:68px;top:10px">© 2026 Kanzlei am Lindenhof Rechtsanwälte</span>
  <span class="abs" style="left:1032px;top:10px">Datenschutz</span>
  <span class="abs" style="left:1106px;top:10px">Impressum</span>
</div>

</body>
</html>
```